Business Card Design Project

Looking to update our business cards. We have a logo with our slogan. We are an IT firm so we wouldlike a modern look.

Industry/Entity Type

Business

```html
<!DOCTYPE html>
<html lang="en">
<head>
<meta charset="utf-8">
<title>Nexora Business Card Presentation</title>
<link rel="stylesheet" href="https://fonts.googleapis.com/css2?family=Jost:wght@400;500;600&display=swap">
<style>
  :root {
    --sheet-bg: #7a4a2c;
    --label-ink: #1c120c;
    --card-white: #ffffff;
    --olive: #5e7a35;
    --olive-dark: #5a7a3c;
    --lime: #abc43f;
    --ink: #2a2a2a;
    --tech-deep: #15287a;
    --tech-mid: #2f62c8;
    --tech-glow: #e6f1ff;
  }
  * { margin: 0; padding: 0; box-sizing: border-box; }
  html, body { width: 1200px; height: 788px; overflow: hidden; }
  body {
    background: var(--sheet-bg);
    font-family: "Jost", "Futura", sans-serif;
    position: relative;
  }
  .view-label {
    position: absolute;
    width: 525px;
    text-align: center;
    font-size: 22px;
    font-weight: 400;
    color: var(--label-ink);
  }
  .card {
    position: absolute;
    width: 525px;
    height: 300px;
    border-radius: 22px;
    overflow: hidden;
    background: var(--card-white);
  }
  .card--front { left: 51px; top: 79px; }
  .card--back-white { left: 621px; top: 79px; }
  .card--back-lime { left: 50px; top: 454px; background: var(--lime); }
  .card--back-tech { left: 621px; top: 454px; }

  .tech-art {
    position: absolute; inset: 0;
    background:
      radial-gradient(ellipse 42% 48% at 45% 52%, var(--tech-glow) 0%, #9cc4f4 30%, rgba(60,110,210,0) 72%),
      linear-gradient(100deg, var(--tech-deep) 0%, var(--tech-mid) 45%, #3a56b8 75%, var(--tech-deep) 100%);
  }

  /* Front */
  .front-block { position: absolute; left: 0; top: 67px; width: 29px; height: 47px; background: var(--olive); }
  .front-band { position: absolute; left: 267px; top: 67px; width: 258px; height: 47px; background: var(--lime); }
  .holder { position: absolute; right: 20px; top: 70px; text-align: right; color: var(--ink); }
  .holder__name { font-size: 17px; line-height: 20px; }
  .holder__role { font-size: 13px; line-height: 18px; }

  .brand { position: absolute; text-align: center; color: var(--olive-dark); }
  .brand__name { font-weight: 500; letter-spacing: 0.12em; line-height: 1; }
  .brand__tagline { font-weight: 600; letter-spacing: 0.2em; margin-top: 4px; }
  .brand--front { left: 34px; top: 66px; width: 232px; }
  .brand--front .brand__name { font-size: 34px; }
  .brand--front .brand__tagline { font-size: 10px; letter-spacing: 0.14em; }
  .brand--large { left: 0; width: 525px; top: 112px; }
  .brand--large .brand__name { font-size: 50px; }
  .brand--large .brand__tagline { font-size: 13px; margin-top: 8px; }

  .contact-list { position: absolute; left: 35px; top: 196px; list-style: none; color: var(--ink); font-size: 14px; }
  .contact-list li { display: flex; align-items: center; height: 22px; }
  .contact-list svg { width: 12px; height: 12px; margin-right: 7px; }
  .address { position: absolute; right: 20px; top: 228px; text-align: right; font-size: 14px; line-height: 18px; color: var(--ink); }
</style>
</head>
<body>
  <div class="view-label" style="left:51px; top:32px;">Front</div>
  <div class="view-label" style="left:621px; top:32px;">Back - 1</div>
  <div class="view-label" style="left:50px; top:403px;">Back - 2</div>
  <div class="view-label" style="left:621px; top:403px;">Back - 3</div>

  <section class="card card--front">
    <div class="front-block"></div>
    <div class="front-band"></div>
    <div class="brand brand--front">
      <div class="brand__name">NEXORA</div>
      <div class="brand__tagline">MAKING TECH EFFORTLESS</div>
    </div>
    <div class="holder">
      <div class="holder__name">Your Name</div>
      <div class="holder__role">Designation</div>
    </div>
    <ul class="contact-list">
      <li><svg viewBox="0 0 12 12"><path d="M3 1l2 2-1 1.5c.6 1.3 1.6 2.3 2.9 2.9L8.4 6.4l2 2-1.3 1.6C5.5 9.8 2.2 6.5 2 2.3z" fill="none" stroke="#333" stroke-width="1"/></svg>+12 345 67890</li>
      <li><svg viewBox="0 0 12 12"><rect x="1" y="5" width="10" height="5" rx="1" fill="#333"/><rect x="3" y="2" width="6" height="3" fill="none" stroke="#333"/></svg>+12 345 67890</li>
      <li><svg viewBox="0 0 12 12"><rect x="1" y="3" width="10" height="7" rx="1" fill="#333"/><path d="M1.5 3.5L6 7l4.5-3.5" fill="none" stroke="#fff" stroke-width="1"/></svg>info@website.com</li>
      <li><svg viewBox="0 0 12 12"><circle cx="6" cy="6" r="4.5" fill="none" stroke="#333"/><path d="M1.5 6h9M6 1.5c-2 2.5-2 6.5 0 9M6 1.5c2 2.5 2 6.5 0 9" fill="none" stroke="#333" stroke-width=".8"/></svg>www.website.com</li>
    </ul>
    <div class="address">#0000, Street Name<br>Area Name<br>Country Code</div>
  </section>

  <section class="card card--back-white">
    <div class="brand brand--large">
      <div class="brand__name">NEXORA</div>
      <div class="brand__tagline">MAKING TECH EFFORTLESS</div>
    </div>
  </section>

  <section class="card card--back-lime">
    <div class="brand brand--large">
      <div class="brand__name">NEXORA</div>
      <div class="brand__tagline">MAKING TECH EFFORTLESS</div>
    </div>
  </section>

  <section class="card card--back-tech">
    <div class="tech-art" role="img" aria-label="Abstract blue technology artwork with glowing light swirls, binary digits and a wireframe globe"></div>
    <div class="brand brand--large">
      <div class="brand__name">NEXORA</div>
      <div class="brand__tagline">MAKING TECH EFFORTLESS</div>
    </div>
  </section>
</body>
</html>
```